A website for a Maltese Law Firm

Our law firm needs a website to further its business. The site should have a simple yet effective design. We would need the following sections: About us, Practice Areas, About Malta, Contact. These should be further split as follows:

About us: Our firm, Our values, What others say, Offices

Practice Areas: Crimimal, Citizenship & Residence, Sovereign Patron Pathway, Criminal Defence, Civil Litigation, Arbitration and ADR, Commercial and Corporate, Media Law.

About Malta: just one section.

Contact: Just one section

We would also need a news feed at the front of the site to include latest news regarding our cases.

At the bottom we need a section for our Terms and a Privacy Statement.

Our logo is being attached.

Target Market(s)

All clients looking for legal assistance in Malta

Industry/Entity Type

Legal

Coding

Coded - Design and coding required

Number of Pages Required

1 page

Requirements
Must have
• It must be simple yet striking.

```html
<!DOCTYPE html>
<html lang="en">
<head>
<meta charset="utf-8">
<title>Calleja &amp; Zerafa Advocates</title>
<link href="https://fonts.googleapis.com/css2?family=Noto+Serif:wght@400;700&family=Noto+Sans:wght@400;700&family=Exo+2:wght@400;500&display=swap" rel="stylesheet">
<style>
:root{
  --brown:#3b1d12;
  --brown-deep:#331a10;
  --ink:#1c1c1c;
  --text:#6b6b6b;
  --rule:#e2e2e2;
  --dark:#202020;
  --darker:#0e0e0e;
  --white:#fff;
}
*{margin:0;padding:0;box-sizing:border-box}
html,body{width:1200px;height:2571px;overflow:hidden;background:var(--white)}
body{position:relative;font-family:"Noto Sans",Arial,sans-serif;color:var(--text)}
.abs{position:absolute}

/* header */
.brand{left:111px;top:58px;display:flex;align-items:center;gap:12px;font-family:"Noto Serif",Georgia,serif;font-size:25px;line-height:1;color:var(--ink)}
.brand-square{width:18px;height:18px;background:var(--brown)}
.call{right:111px;top:70px;display:flex;align-items:center;gap:10px;font-size:22px;color:var(--ink)}
.call-icon{width:26px;height:26px;background:var(--brown);border-radius:4px;display:flex;align-items:center;justify-content:center}

/* hero */
.hero{left:0;top:123px;width:1200px;height:566px;background:linear-gradient(120deg,#d4d1cc 0%,#b8aba0 30%,#8a7a70 55%,#3a3a42 80%,#2a2a30 100%)}
.nav{left:111px;top:123px;width:978px;height:74px;display:flex;background:rgba(20,20,20,.55)}
.nav a{font-family:"Noto Serif",Georgia,serif;font-size:13px;color:var(--white);text-decoration:none;display:flex;align-items:center;justify-content:center;border-left:1px solid rgba(255,255,255,.35);height:100%}
.nav a:last-child{border-right:1px solid rgba(255,255,255,.35)}
.nav a.active{background:var(--brown)}
.caption{left:111px;top:459px;height:110px;display:flex}
.caption-mark{width:115px;height:110px;background:var(--white);display:flex;align-items:center;justify-content:center}
.caption-text{width:398px;background:rgba(59,29,18,.85);color:var(--white);font-family:"Exo 2",Arial,sans-serif;font-size:30px;line-height:38px;padding:17px 0 0 38px;text-transform:uppercase}
.dots{left:140px;top:640px;display:flex;gap:8px}
.dots span{width:8px;height:8px;border-radius:50%;background:rgba(255,255,255,.5)}
.dots span.on{background:var(--brown)}

/* sections */
.section-title{font-family:"Noto Serif",Georgia,serif;font-weight:400;color:var(--ink);font-size:27px;text-align:center;width:1200px;left:0}
.welcome-text{left:111px;top:788px;width:978px;text-align:center;font-size:12px;line-height:31px}
.rule{left:0;width:1200px;height:1px;background:var(--rule)}

.practice{top:1001px;width:220px}
.practice .photo{width:220px;height:139px}
.practice h3{font-family:"Noto Serif",Georgia,serif;font-weight:400;font-size:15px;color:var(--ink);margin-top:27px}
.practice p{font-size:11px;line-height:26px;margin-top:8px}
.more{font-size:12px;color:var(--ink);display:flex;align-items:center;gap:6px;margin-top:16px}
.more i{width:12px;height:12px;border-radius:50%;background:var(--ink);display:inline-flex;align-items:center;justify-content:center}

.news-bar{left:0;top:1328px;width:1200px;height:77px;background:var(--dark)}
.news-bar h2{font-family:"Noto Serif",Georgia,serif;font-weight:400;color:var(--white);font-size:27px;text-align:center;line-height:77px}
.news-notch{left:592px;top:1404px;width:0;height:0;border-left:8px solid transparent;border-right:8px solid transparent;border-top:9px solid var(--dark)}
.news-band{left:0;top:1405px;width:1200px;height:283px;background:var(--brown-deep)}
.news-card{top:1469px;width:455px;height:171px;background:var(--white);padding:14px 16px 0 218px}
.news-card h4{font-family:"Noto Serif",Georgia,serif;font-weight:400;font-size:14px;line-height:26px;color:var(--ink)}
.news-card p{font-size:12px;line-height:24px;margin-top:6px}
.news-photo{top:1443px;width:223px;height:172px}

.cases-title{left:111px;top:1722px;font-family:"Noto Serif",Georgia,serif;font-weight:400;font-size:26px;color:var(--ink)}
.case{left:111px;width:620px;height:140px;border-bottom:1px solid var(--rule)}
.case-photo{width:168px;height:111px;position:absolute;left:0;top:0;box-shadow:0 4px 8px rgba(0,0,0,.35)}
.case-date{position:absolute;left:0;bottom:0;width:168px;height:34px;background:rgba(0,0,0,.7);color:var(--white);font-size:13px;text-align:center;line-height:34px}
.case-body{position:absolute;left:189px;top:0;width:431px}
.case-lead{font-size:12.5px;line-height:26px;color:var(--ink)}
.case-body p.sub{font-size:11.5px;line-height:26px;margin-top:8px}

.contact-box{left:768px;top:1733px;width:321px;height:343px;border:1px solid #d8d8d8;padding:0 27px}
.contact-box h3{font-family:"Noto Serif",Georgia,serif;font-weight:400;font-size:21px;color:var(--ink);margin-top:25px;margin-bottom:13px}
.field{width:267px;height:40px;border:1px solid #cfcfcf;background:linear-gradient(#fafafa,#e7e7e7);font-size:11px;color:#9a9a9a;padding:11px 16px;margin-bottom:11px;box-shadow:inset 0 1px 2px rgba(0,0,0,.1)}
.field.tall{height:72px}
.submit{width:113px;height:44px;background:var(--brown-deep);color:var(--white);font-size:13px;text-align:center;line-height:44px;border-radius:3px;margin:13px auto 0}

/* footer */
.footer{left:0;top:2117px;width:1200px;height:207px;background:var(--dark)}
.fcol{top:2140px;color:var(--white)}
.fcol h5{font-family:"Noto Serif",Georgia,serif;font-weight:400;font-size:16px;letter-spacing:.5px;margin-bottom:14px}
.fcol li{list-style:none;font-size:12px;line-height:20px;display:flex;align-items:flex-start;gap:10px}
.social li{line-height:26px}
.links li{line-height:34px}
.fcol .sq{width:13px;height:13px;margin-top:6px;border-radius:2px}
.sub-field{width:264px;height:39px;background:var(--white);border-radius:3px;font-size:11px;color:#9a9a9a;padding:12px 15px;margin-top:12px}
.sub-btn{width:118px;height:36px;background:var(--darker);font-size:12px;text-align:center;line-height:36px;margin-top:9px}
.copy{left:0;top:2324px;width:1200px;height:79px;background:var(--darker);color:var(--white);font-size:12.5px;text-align:center;line-height:79px}

.terms{left:111px;top:2436px;width:978px}
.terms h6{font-family:"Noto Serif",Georgia,serif;font-weight:400;font-size:14px;color:var(--ink);letter-spacing:.5px}
.terms p{font-size:11.5px;line-height:25px;margin-top:12px}
</style>
</head>
<body>

<header>
  <div class="abs brand"><span class="brand-square"></span><span>Calleja &amp; Zerafa Advocates</span></div>
  <div class="abs call">
    <span class="call-icon"><svg width="14" height="14" viewBox="0 0 24 24"><path fill="#fff" d="M6.6 10.8a15.1 15.1 0 0 0 6.6 6.6l2.2-2.2c.3-.3.7-.4 1-.2 1.1.4 2.3.6 3.6.6.6 0 1 .4 1 1V20c0 .6-.4 1-1 1C10.6 21 3 13.4 3 4c0-.6.4-1 1-1h3.5c.6 0 1 .4 1 1 0 1.3.2 2.5.6 3.6.1.3 0 .7-.2 1z"/></svg></span>
    <span>CALL NOW : (356) 2000 4815</span>
  </div>
</header>

<section class="abs hero" role="img" aria-label="Photo of lawyers' hands signing documents at a desk"></section>
<nav class="abs nav">
  <a class="active" style="width:171px" href="#">HOME</a>
  <a style="width:171px" href="#">ABOUT US</a>
  <a style="width:223px" href="#">PRACTICE AREAS</a>
  <a style="width:209px" href="#">ABOUT MALTA</a>
  <a style="width:204px" href="#">CONTACT US</a>
</nav>
<div class="abs caption">
  <div class="caption-mark"><svg width="38" height="34" viewBox="0 0 38 34"><path d="M3 3l14 14L3 31M19 3l14 14-14 14" fill="none" stroke="#3b1d12" stroke-width="5"/></svg></div>
  <div class="caption-text">Sovereign Patron<br>Pathway</div>
</div>
<div class="abs dots"><span class="on"></span><span></span><span></span></div>

<section>
  <h1 class="abs section-title" style="top:741px">WELCOME TO CZ ADVOCATES</h1>
  <p class="abs welcome-text">Lorem ipsum dolor sit amet, consectetuer adipiscing elit, sed diam nonummy nibh euismod tincidunt ut laoreet dolore magna aliquam erat volutpat. Ut wisi enim ad minim veniam, quis nostrud exerci tation ullamcorper suscipit lobortis nisl ut aliquip ex ea commodo consequat. Duis autem vel eum iriure dolor in hendrerit in vulputate velit esse molestie cons equat, vel illum dolore eu feugiat nulla facilisis at vero eros et accumsan et iusto odio dignissim.</p>
</section>
<div class="abs rule" style="top:908px"></div>

<section>
  <h2 class="abs section-title" style="top:944px">PRACTICE AREAS</h2>
  <article class="abs practice" style="left:111px">
    <div class="photo" role="img" aria-label="Photo of police officers making an arrest" style="background:linear-gradient(135deg,#6a6f78,#c9ccd1 55%,#3c4048)"></div>
    <h3>CRIMIMAL</h3>
    <p>Lorem ipsum dolor sit amet, consectetur adipiscing elit. Donec ac mi elit.</p>
    <div class="more"><i><svg width="6" height="6" viewBox="0 0 6 6"><path d="M1 0l4 3-4 3z" fill="#fff"/></svg></i>VIEW DETAILS</div>
  </article>
  <article class="abs practice" style="left:363px">
    <div class="photo" role="img" aria-label="Photo of scales of justice and a gavel on law books" style="background:linear-gradient(160deg,#4a2a20,#8a6a4e 50%,#d8cdbf)"></div>
    <h3>CITIZENSHIP &amp; RESIDENCE</h3>
    <p>Lorem ipsum dolor sit amet, consectetur adipiscing elit. Donec ac mi elit.</p>
    <div class="more"><i><svg width="6" height="6" viewBox="0 0 6 6"><path d="M1 0l4 3-4 3z" fill="#fff"/></svg></i>VIEW DETAILS</div>
  </article>
  <article class="abs practice" style="left:615px">
    <div class="photo" role="img" aria-label="Photo of stacked legal files" style="background:linear-gradient(135deg,#6b4b12,#c9a040 50%,#e8d39a)"></div>
    <h3>CRIMINAL DEFENCE</h3>
    <p>Lorem ipsum dolor sit amet, consectetur adipiscing elit. Donec ac mi elit.</p>
    <div class="more"><i><svg width="6" height="6" viewBox="0 0 6 6"><path d="M1 0l4 3-4 3z" fill="#fff"/></svg></i>VIEW DETAILS</div>
  </article>
  <article class="abs practice" style="left:867px">
    <div class="photo" role="img" aria-label="Photo of silhouetted business people by an office window" style="background:linear-gradient(180deg,#2c3a4c,#a7c1d8 60%,#1f2733)"></div>
    <h3>CIVIL LITIGATION</h3>
    <p>Lorem ipsum dolor sit amet, consectetur adipiscing elit. Donec ac mi elit.</p>
    <div class="more"><i><svg width="6" height="6" viewBox="0 0 6 6"><path d="M1 0l4 3-4 3z" fill="#fff"/></svg></i>VIEW DETAILS</div>
  </article>
</section>

<section>
  <div class="abs news-bar"><h2>LATEST NEWS</h2></div>
  <div class="abs news-band"></div>
  <div class="abs news-notch"></div>
  <article class="abs news-card" style="left:134px">
    <h4>Mauris quis viverra erat. Integer quis maximus nisl.</h4>
    <p>Lorem ipsum dolor sit amet, consectet ur adipis cing elit. Integer non nulla...</p>
    <div class="more" style="margin-top:6px"><i><svg width="6" height="6" viewBox="0 0 6 6"><path d="M1 0l4 3-4 3z" fill="#fff"/></svg></i>READ MORE</div>
  </article>
  <div class="abs news-photo" style="left:111px;background:linear-gradient(135deg,#c9b7a8,#5c5a5e 55%,#2b2b30)" role="img" aria-label="Photo of hands typing on a laptop"></div>
  <article class="abs news-card" style="left:634px">
    <h4>Mauris quis viverra erat. Integer quis maximus nisl.</h4>
    <p>Lorem ipsum dolor sit amet, consectet ur adipis cing elit. Integer non nulla...</p>
    <div class="more" style="margin-top:6px"><i><svg width="6" height="6" viewBox="0 0 6 6"><path d="M1 0l4 3-4 3z" fill="#fff"/></svg></i>READ MORE</div>
  </article>
  <div class="abs news-photo" style="left:612px;background:linear-gradient(135deg,#2a1a10,#7a5234 50%,#c89a62)" role="img" aria-label="Photo of a gavel and scales on a wooden desk"></div>
</section>

<section>
  <h2 class="abs cases-title">LATEST CASES</h2>
  <article class="abs case" style="top:1783px">
    <div class="case-photo" role="img" aria-label="Photo of handcuffed hands" style="background:linear-gradient(135deg,#3a3a3a,#8a8580 50%,#2a2a2a)"><div class="case-date">May 12, 2016</div></div>
    <div class="case-body">
      <p class="case-lead">Lorem ipsum dolor sit amet, consectetur adipiscing elit. Donec laoreet ipsum ut turpis tincidunt, sed lobortis nunc feugiat.</p>
      <p class="sub">Ut wisi enim ad minim veniam, quis nostrud exerci tation ullamcorper susc ipit lobortis nisl ut aliquip ex ea commodo consequat...</p>
    </div>
  </article>
  <article class="abs case" style="top:1946px">
    <div class="case-photo" role="img" aria-label="Photo of a hooded figure in shadow" style="background:linear-gradient(135deg,#4f5a3a,#2b2b2b 55%,#9aa08a)"><div class="case-date">May 12, 2016</div></div>
    <div class="case-body">
      <p class="case-lead">cursus lacus, nec lacinia eros neque eu eros. Maecenas consectetur pos uere feugiat. Praesent quis leo neque.</p>
      <p class="sub">Ut wisi enim ad minim veniam, quis nostrud exerci tation ullamcorper susc ipit lobortis nisl ut aliquip ex ea commodo consequat...</p>
    </div>
  </article>

  <aside class="abs contact-box">
    <h3>QUICK CONTACT</h3>
    <div class="field">Name</div>
    <div class="field">Email Address</div>
    <div class="field tall">Message</div>
    <div class="submit">SUBMIT</div>
  </aside>
</section>

<footer>
  <div class="abs footer"></div>
  <div class="abs fcol" style="left:115px">
    <h5>GET IN TOUCH</h5>
    <ul>
      <li><svg width="12" height="16" viewBox="0 0 12 16" style="margin-top:2px"><path d="M6 0a6 6 0 0 0-6 6c0 4.5 6 10 6 10s6-5.5 6-10a6 6 0 0 0-6-6zm0 8.5A2.5 2.5 0 1 1 6 3.5a2.5 2.5 0 0 1 0 5z" fill="#fff"/></svg><span>CZ ADVOCATES<br>27/4, Lantern Street,<br>Velletta</span></li>
      <li style="margin-top:14px"><svg width="15" height="11" viewBox="0 0 15 11" style="margin-top:5px"><rect width="15" height="11" rx="1" fill="#fff"/><path d="M0 1l7.5 5L15 1" fill="none" stroke="#202020" stroke-width="1.3"/></svg><span>hello@czadvocates.example</span></li>
      <li style="margin-top:18px"><svg width="15" height="15" viewBox="0 0 24 24" style="margin-top:3px"><rect width="24" height="24" rx="4" fill="#fff"/><path d="M7.6 10.8a12 12 0 0 0 5.6 5.6l1.8-1.8c.3-.3.6-.3.9-.2.9.3 1.9.5 2.9.5v3c-7.5 0-13.6-6.1-13.6-13.6h3c0 1 .2 2 .5 2.9.1.3 0 .6-.2.9z" fill="#202020"/></svg><span>(356) 2000 4815</span></li>
    </ul>
  </div>
  <div class="abs fcol links" style="left:394px">
    <h5>QUICK LINKS</h5>
    <ul><li>About us</li><li>Practice Areas</li><li>About Malta</li><li>Contact us</li></ul>
  </div>
  <div class="abs fcol social" style="left:588px">
    <h5>SOCIAL NETWORKS</h5>
    <ul>
      <li><span class="sq" style="background:#3b5998"></span>Circlefeed</li>
      <li><span class="sq" style="background:#55acee"></span>Chirpline</li>
      <li><span class="sq" style="background:#0e76a8"></span>Prolink</li>
      <li><span class="sq" style="background:#dd4b39"></span>Orbitnet</li>
      <li><span class="sq" style="background:#f26522"></span>RSS</li>
    </ul>
  </div>
  <div class="abs fcol" style="left:825px">
    <h5>NEWSLETTER SIGNUP</h5>
    <p style="font-size:12px;line-height:22px;width:275px">Enter your email address to receive our latest newsletters containing our latest News.</p>
    <div class="sub-field">Email Address</div>
    <div class="sub-btn">SUBSCRIBE</div>
  </div>
  <div class="abs copy">©2016 CZ Advocates. All Right Reserved.</div>

  <div class="abs terms">
    <h6>TERMS AND PRIVACY STATEMENT</h6>
    <p>Sed ornare, libero non venenatis venenatis, velit magna vehicula nulla, nec fringilla nunc massa et urna. Duis tincidunt, arcu quis ultricies maximus, leo sem cursus lacus, nec lacinia eros neque eu eros. Maecenas consectetur posuere feugiat. Praesent quis leo neque. Ut ultricies mauris eget lacinia volutpat. Sed rutrum tincidunt mauris, a ornare mi tempor et. Duis sed massa quis eros egestas euismod in tristique nibh.</p>
  </div>
</footer>

</body>
</html>
```